Hörbuchcover
Zielgruppe
Spiritueller Hörbuchverlag für ganzheitliche Gesundheit, Glück und Wohlstand.
Aufgabenstellung
Benötigt wird ein schönes quadratisches Cover, 2400x2400 mindestens 72dpi für ein Hörbuchcover.
Auf dem Cover soll eine gelb/orange Rose zu in Form einer Blüte zu sehen sein.
Titel: Goldener Pfad
Untertitel: Emotionen sind der Schlüssel für Gesundheit, Energie & Lebensfreude
Autorenname: Dr. med. Katrin Wollberg
Das Velmira Logo soll unten mittig sitzen.
Es folgen weiterer Hörbücher von dieser Autorin und es wäre gut wenn man die folgenden Cover in einem ähnlichen Stil halten könnte. Ein harmonisches und gut zu erkennendes Design mit hohem Wiedererkennungseffekt. Ich freue mich auf kreative Designvorschläge.
Auf velmira.de kann man sehen wo das Logo sitzen soll.
Herzliche Grüße - Jonas

```html
<!DOCTYPE html>
<html lang="de">
<head>
<meta charset="utf-8">
<title>Goldener Pfad – Hörbuchcover</title>
<link href="https://fonts.googleapis.com/css2?family=Quicksand:wght@400;500;700&display=swap" rel="stylesheet">
<style>
  :root {
    --green-edge: #86bc4c;
    --green-mid: #b4d68e;
    --glow: #f6faef;
    --ink: #1d1d1b;
    --title-fill: #ffffff;
    --title-shadow: #1d1d1b;
    --rose-cream: #fbeed2;
    --rose-yellow: #f2c25a;
    --rose-orange: #e4714a;
    --rose-blush: #f3ddd6;
  }
  * { margin: 0; padding: 0; box-sizing: border-box; }
  html, body { width: 1200px; height: 1200px; overflow: hidden; }
  body { font-family: "Quicksand", sans-serif; }

  .cover {
    position: relative;
    width: 1200px;
    height: 1200px;
    background: radial-gradient(circle at 50% 64%, var(--glow) 0%, var(--green-mid) 40%, var(--green-edge) 72%);
    overflow: hidden;
  }

  .rose {
    position: absolute;
    left: 255px;
    top: 152px;
    width: 745px;
    height: 630px;
    border-radius: 48% 52% 46% 54% / 55% 50% 50% 45%;
    background: radial-gradient(ellipse at 56% 38%, var(--rose-cream) 0%, var(--rose-yellow) 38%, var(--rose-orange) 62%, var(--rose-blush) 85%, rgba(243,221,214,0) 100%);
  }

  .title-arc {
    position: absolute;
    inset: 0;
    width: 1200px;
    height: 1200px;
    z-index: 2;
  }
  .title-arc text {
    font-family: "Quicksand", sans-serif;
    font-weight: 400;
    font-size: 112px;
    letter-spacing: 18px;
    fill: var(--title-fill);
  }
  .title-arc .title-shadow { fill: var(--title-shadow); }

  .subtitle {
    position: absolute;
    left: 0;
    right: 0;
    top: 806px;
    text-align: center;
    color: var(--ink);
    font-weight: 400;
    font-size: 42px;
    line-height: 60px;
    letter-spacing: 2.5px;
  }

  .author {
    position: absolute;
    left: 764px;
    top: 958px;
    color: var(--ink);
    font-weight: 700;
    font-size: 38px;
    line-height: 50px;
  }

  .publisher {
    position: absolute;
    left: 0;
    right: 0;
    top: 1043px;
    display: flex;
    flex-direction: column;
    align-items: center;
    gap: 30px;
  }
  .publisher-mark {
    width: 74px;
    height: 74px;
    border-radius: 50%;
    background: var(--ink);
  }
  .publisher-name {
    color: var(--ink);
    font-weight: 700;
    font-size: 34px;
    letter-spacing: 4px;
    text-transform: uppercase;
    line-height: 1;
  }
</style>
</head>
<body>
  <main class="cover">
    <div class="rose" role="img" aria-label="Geöffnete gelb-orange Rosenblüte mit cremefarbenem Kern und rötlichen Blatträndern"></div>

    <svg class="title-arc" viewBox="0 0 1200 1200" aria-label="Goldener Pfad">
      <defs>
        <path id="title-curve" d="M -136 851 A 736 736 0 0 1 1336 851" fill="none"/>
        <path id="title-curve-shadow" d="M -132 855 A 736 736 0 0 1 1340 855" fill="none"/>
      </defs>
      <text class="title-shadow"><textPath href="#title-curve-shadow" startOffset="50%" text-anchor="middle">Goldener Pfad</textPath></text>
      <text><textPath href="#title-curve" startOffset="50%" text-anchor="middle">Goldener Pfad</textPath></text>
    </svg>

    <p class="subtitle">Emotionen sind der Schlüssel für<br>Gesundheit, Energie &amp; Lebensfreude</p>

    <p class="author">Dr. med.<br>Katrin Wollberg</p>

    <div class="publisher">
      <span class="publisher-mark"></span>
      <span class="publisher-name">Velmira</span>
    </div>
  </main>
</body>
</html>
```